Business Card- Can you make it cool vs boring!

Need a refresh on my business card! Want it to be modern but simple, classic and a pop of coolness! we do senior living and it is boring. but that doesn't mean our business card have to look boring! Open to two sided cards. our website is www.Dunmere-PK.com

Target Market(s)

capital market

Industry/Entity Type

senior housing/ real estate

Contact Information for Business Card

logo/ name/ cell/ address/ www.Dunmere-PK.com/ space for a QR code

Requirements
Must have
• maybe a QR code (do not make prominent I may not use the QR so design where it can be taken out) that link to more about us/ landing page. needs to be modern but clean
Should not have
• clip art or script

```html
<!DOCTYPE html>
<html lang="en">
<head>
<meta charset="utf-8">
<title>Dunmere Living – Business Card</title>
<link href="https://fonts.googleapis.com/css2?family=Kalam:wght@400&family=Open+Sans:wght@700&display=swap" rel="stylesheet">
<style>
  :root {
    --brand: #a82e00;
    --accent-line: #d9360f;
    --card-white: #ffffff;
    --stage: #d7e4e0;
    --ink-light: #ffffff;
  }
  * { margin: 0; padding: 0; box-sizing: border-box; }
  html, body { width: 1200px; height: 1200px; overflow: hidden; }
  body {
    background: var(--stage);
    position: relative;
    font-family: "Kalam", cursive;
  }
  .card {
    position: absolute;
    left: 189px;
    width: 822px;
    height: 506px;
    border-radius: 60px;
    overflow: hidden;
  }
  .card--front { top: 80px; background: var(--card-white); }
  .card--back { top: 628px; background: var(--brand); }

  .front-band {
    position: absolute; left: 0; top: 86px;
    width: 590px; height: 334px;
  }
  .contact {
    position: absolute; left: 76px; top: 112px;
    color: var(--ink-light);
  }
  .contact__name {
    font-family: "Open Sans", sans-serif;
    font-weight: 700;
    font-size: 52px;
    line-height: 1;
    letter-spacing: -0.5px;
  }
  .contact__role {
    font-size: 40px;
    line-height: 1;
    margin-top: 12px;
  }
  .contact__list { list-style: none; margin-top: 22px; }
  .contact__item {
    display: flex; align-items: center;
    font-size: 31px; line-height: 53px;
    margin-left: 4px;
  }
  .contact__icon { width: 22px; height: 26px; margin-right: 14px; flex: none; }

  .brand-name {
    position: absolute;
    color: var(--brand);
    font-size: 38px;
    line-height: 1;
    white-space: nowrap;
    text-align: center;
  }
  .card--front .brand-name { left: 544px; top: 100px; width: 250px; }

  .qr-slot {
    position: absolute; left: 620px; top: 181px;
    width: 144px; height: 144px;
    border: 3px solid var(--accent-line);
    display: flex; align-items: center; justify-content: center;
    text-align: center;
    color: var(--brand);
    font-size: 25px; line-height: 1.2;
  }

  .back-band {
    position: absolute; left: 0; top: 186px;
    width: 100%; height: 140px;
    background: var(--card-white);
  }
  .card--back .brand-name {
    left: 0; width: 100%; top: 234px; font-size: 44px;
  }
  .back-web {
    position: absolute; left: 0; width: 100%; top: 336px;
    display: flex; justify-content: center; align-items: center;
    color: var(--ink-light);
    font-size: 17px;
  }
  .back-web .contact__icon { width: 14px; height: 14px; margin-right: 6px; }
</style>
</head>
<body>

<section class="card card--front" aria-label="Business card front">
  <svg class="front-band" viewBox="0 0 590 334" aria-hidden="true">
    <polygon points="0,0 486,0 587,164 496,334 0,334" fill="var(--brand)"/>
  </svg>

  <div class="contact">
    <h1 class="contact__name">Your Name</h1>
    <p class="contact__role">Designation</p>
    <ul class="contact__list">
      <li class="contact__item">
        <svg class="contact__icon" viewBox="0 0 22 26" aria-hidden="true">
          <rect x="2" y="0" width="18" height="26" rx="3" fill="#fff"/>
          <rect x="8" y="20" width="6" height="2.5" rx="1" fill="var(--brand)"/>
        </svg>
        Your Contact Number
      </li>
      <li class="contact__item">
        <svg class="contact__icon" viewBox="0 0 22 26" aria-hidden="true">
          <path d="M11 0C5 0 1 4.5 1 10c0 7 10 16 10 16s10-9 10-16C21 4.5 17 0 11 0z" fill="#fff"/>
          <circle cx="11" cy="10" r="3.6" fill="var(--brand)"/>
        </svg>
        Your Address
      </li>
      <li class="contact__item">
        <svg class="contact__icon" viewBox="0 0 24 24" aria-hidden="true">
          <circle cx="12" cy="12" r="12" fill="#fff"/>
          <path d="M12 0v24M0 12h24M12 0c-5 4-5 20 0 24M12 0c5 4 5 20 0 24" stroke="var(--brand)" stroke-width="2" fill="none"/>
        </svg>
        www.Dunmere-PK.com
      </li>
    </ul>
  </div>

  <p class="brand-name">Dunmere Living</p>
  <div class="qr-slot">QR<br>Here</div>
</section>

<section class="card card--back" aria-label="Business card back">
  <div class="back-band"></div>
  <p class="brand-name">Dunmere Living</p>
  <p class="back-web">
    <svg class="contact__icon" viewBox="0 0 24 24" aria-hidden="true">
      <circle cx="12" cy="12" r="12" fill="#fff"/>
      <path d="M12 0v24M0 12h24M12 0c-5 4-5 20 0 24M12 0c5 4 5 20 0 24" stroke="var(--brand)" stroke-width="2" fill="none"/>
    </svg>
    www.Dunmere-PK.com
  </p>
</section>

</body>
</html>
```